Brookvale Building Company - advertisement poster

I am looking to print some canvas signs to advertise my general contracting company, Brookvale Building Company. The sign will measure 6' long x 3' high so the size should match that ratio. I already have a logo icon, which is the Letter 'B' and some trees that I would like to incorporate, see attached. I would also like the to have the following information listed:
1) phone number: 831-555-0172
2) email: brookvalebuildingcompany@mailnest.example
3) website: brookvalebuildingcompany.example
4) Lic#4826130
5) I want to use this text: "BUILD WITH THE B-CREW!"

The ad should be relatively simple and clean. Black and Green are my company colors. I am open to creative ideas!

Target Market(s)

People looking to renovate their homes

Industry/Entity Type

Construction

Colors
59FF00
82FF00
B8FF75
E3FFCB
F4FFEA

Requirements
Must have
• Must have my company logo
Should not have
• No photos or complex graphics

```html
<!DOCTYPE html>
<html lang="en">
<head>
<meta charset="utf-8">
<title>Brookvale Building Company – Sign</title>
<link rel="stylesheet" href="https://fonts.googleapis.com/css2?family=Montserrat:wght@700;800&display=swap">
<style>
  :root {
    --bg: #e8ebe6;
    --green: #6cb43f;
    --green-light: #8dc63f;
    --white: #ffffff;
    --navy: #1f1f6b;
  }
  html, body {
    margin: 0;
    width: 1200px;
    height: 800px;
    overflow: hidden;
    background: var(--bg);
  }
  .sign {
    position: absolute;
    left: 50px;
    top: 125px;
    width: 1100px;
    height: 550px;
    display: block;
    box-shadow: 0 10px 30px rgba(0,0,0,0.18);
  }
  .sign text {
    font-family: "Montserrat", Arial, sans-serif;
    fill: var(--navy);
  }
  .headline-top { font-size: 58px; font-weight: 800; }
  .headline-main { font-size: 98px; font-weight: 800; }
  .website { font-size: 29px; font-weight: 700; }
  .phone { font-size: 52px; font-weight: 800; }
  .brand-name { font-size: 44px; font-weight: 800; }
  .brand-sub { font-size: 17px; font-weight: 800; letter-spacing: 4px; }
  .contact-detail { font-size: 15px; font-weight: 700; }
  .icon { fill: none; stroke: var(--navy); stroke-width: 2.6; }
</style>
</head>
<body>
<svg class="sign" viewBox="0 0 1100 550" xmlns="http://www.w3.org/2000/svg" aria-label="Brookvale Building Company sign">
  <rect class="panel-green" x="0" y="0" width="1100" height="550" fill="var(--green)"/>
  <polygon class="panel-white" points="737,0 1100,0 1100,462 858,462 583,115 781,132" fill="var(--white)"/>
  <polygon class="band-contact" points="649,462 1100,462 1100,550 704,550" fill="var(--green-light)"/>

  <g class="brand">
    <rect x="904" y="70" width="62" height="62" fill="var(--green)"/>
    <text class="brand-name" x="935" y="190" text-anchor="middle" textLength="290" lengthAdjust="spacingAndGlyphs">BROOKVALE</text>
    <text class="brand-sub" x="935" y="220" text-anchor="middle" textLength="290" lengthAdjust="spacing">BUILDING COMPANY</text>
  </g>

  <g class="details">
    <text class="contact-detail" x="935" y="272" text-anchor="middle" textLength="310" lengthAdjust="spacingAndGlyphs">brookvalebuildingcompany@mailnest.example</text>
    <text class="contact-detail" x="935" y="298" text-anchor="middle">Lic#4826130</text>
  </g>

  <text class="headline-top" x="48" y="268" textLength="515" lengthAdjust="spacingAndGlyphs">BUILD WITH THE</text>
  <text class="headline-main" x="44" y="378" textLength="680" lengthAdjust="spacing">B-CREW!</text>

  <g class="icon globe" transform="translate(70,505)">
    <circle cx="0" cy="0" r="15"/>
    <ellipse cx="0" cy="0" rx="7" ry="15"/>
    <line x1="-15" y1="0" x2="15" y2="0"/>
    <line x1="-13" y1="-7" x2="13" y2="-7"/>
    <line x1="-13" y1="7" x2="13" y2="7"/>
  </g>
  <text class="website" x="100" y="516">brookvalebuildingcompany.example</text>

  <g class="phone-icon" transform="translate(735,498)">
    <path d="M-12,-10 l6,-4 l5,8 l-4,3 q2,6 8,10 l3,-4 l8,5 l-4,6 q-16,-2 -22,-24z" fill="var(--navy)"/>
    <path d="M4,-14 a12,12 0 0 1 12,12" class="icon" stroke-width="2.4"/>
    <path d="M4,-7 a6,6 0 0 1 6,6" class="icon" stroke-width="2.4"/>
  </g>
  <text class="phone" x="768" y="518" textLength="310" lengthAdjust="spacingAndGlyphs">831.555.0172</text>
</svg>
</body>
</html>
```